Business Card Design for Vintage Jazz

I am a vintage jazz band leader in New York City. My groups play the music of the 1920s, 1930s and 1940s. My website is morvalquist.com for more info on what I do.

I am looking for a two sided business card design that has the look and feel of a really nice business card from the 1930s. I need to convey with the design that my work has that vintage kind of class and style, but also conveys that we are fun and entertaining.

Most importantly it should make a bold staement. If Hal Denbrook had a card, what would it have looked like? I want a card that I feel confident will make an impact and will let people know that my work is te the top that NYC has to offer in vintage jazz..

Note that I have only decided to avoid the "committed payment" option as I have not used this service before. Assuming that I get quality work I will select a design from those presented.

Target Market(s)

people who want to hire my band for events, media, and new fans of the band

Industry/Entity Type

Performing Art

Contact Information for Business Card

Definitely a matte finish, possibly a sort of old style of paper with that brown tint? definitely a thick card.

Requirements
Must have
• FRONT
• My name: Tobin Vashley
• What I do: Bandleader, Guitarist, Vocalist, Songwriter
• Contact Details: morvalquist.com tobin@morvalquist.com 646-555-0148
• BACK
• My Social Media Links:
• facebook.morvalquist.com
• twitter, instagram, linkedin: morvalquist
• I'm also including a photo image I would like to use. The photo's background is not needed, and to be honest isn't really desireable. Just looking to use the image of me.
Nice to have
• I'm attaching which could be used as is, omitted from the card, or altered maybe with text going around the outside of the circle or in some other way. It may need some clean up to the edges of the lettering as we only use it for the website thumbnail.
• If there's space I'd like to include the text "join our mailing list for a free song download: freesong.morvalquist.com" If not perhaps just "Download a Free Song at: freesong.morvalquist.com - something to this end.
Should not have
• anything cartoony. Don't think retro 90s's vision of the swing era, think actual swing era!
• anything modern. Got to look old school
• Try to avoid dark backgrounds. Since we often play in bars and clubs where it is dar, a d
• avoid script fonts.

```html
<!DOCTYPE html>
<html lang="en">
<head>
<meta charset="utf-8">
<title>Tobin Vashley – Business Card</title>
<link rel="stylesheet" href="https://fonts.googleapis.com/css2?family=Josefin+Sans:wght@400;600;700&display=swap">
<style>
  :root {
    --stage: #666666;
    --paper-front: #f1e8d4;
    --paper-back: #e4d5b6;
    --ink: #1f1a13;
    --ink-soft: #3a3024;
    --rule: #8a7350;
  }
  * { margin: 0; padding: 0; box-sizing: border-box; }
  html, body { width: 1200px; height: 900px; overflow: hidden; }
  body {
    background: var(--stage);
    font-family: "Josefin Sans", "Futura", Arial, sans-serif;
    position: relative;
    color: var(--ink);
  }
  .card {
    position: absolute;
    top: 200px;
    width: 310px;
    height: 502px;
  }
  .card::before {
    content: "";
    position: absolute;
    inset: 12px;
    border: 1px solid var(--rule);
    border-radius: inherit;
    pointer-events: none;
  }
  .card::after {
    content: "";
    position: absolute;
    inset: 17px;
    border: 0.5px solid var(--rule);
    border-radius: inherit;
    opacity: 0.6;
    pointer-events: none;
  }
  .card--front {
    left: 265px;
    background: var(--paper-front);
    border-radius: 62px 0 62px 0;
  }
  .card--back {
    left: 641px;
    width: 309px;
    background: var(--paper-back);
    border-radius: 0 62px 0 62px;
  }
  .wordmark {
    position: absolute;
    top: 80px;
    width: 160px;
    font-weight: 600;
    font-size: 26px;
    line-height: 1.1;
    letter-spacing: 2px;
    text-transform: uppercase;
    text-align: right;
    color: var(--ink);
  }
  .card--front .wordmark { left: 84px; }
  .card--back .wordmark { left: 104px; }
  .deco-rule {
    position: absolute;
    height: 1px;
    background: var(--rule);
  }
  .card--front .deco-rule { left: 84px; top: 152px; width: 160px; }
  .card--back .deco-rule { left: 104px; top: 152px; width: 160px; }
  .holder-name {
    position: absolute;
    left: 43px;
    top: 370px;
    font-size: 19px;
    font-weight: 600;
    letter-spacing: 1px;
  }
  .contact-list, .social-list { list-style: none; position: absolute; }
  .contact-list { left: 43px; top: 414px; }
  .contact-list li {
    display: flex;
    align-items: center;
    height: 18.5px;
    font-size: 13.5px;
    color: var(--ink-soft);
  }
  .contact-list svg { width: 10px; height: 10px; margin-right: 8px; fill: var(--ink); flex: none; }
  .social-list { left: 29px; top: 305px; }
  .social-list li {
    display: flex;
    align-items: center;
    height: 22.5px;
    font-size: 13.5px;
    color: var(--ink-soft);
  }
  .social-mark {
    width: 13px;
    height: 13px;
    border: 1.5px solid var(--ink);
    border-radius: 2px;
    margin-right: 7px;
    flex: none;
  }
  .roles {
    position: absolute;
    left: 31px;
    top: 403px;
    font-size: 16px;
    font-weight: 700;
    line-height: 23px;
    letter-spacing: 0.5px;
  }
</style>
</head>
<body>
  <section class="card card--front" aria-label="Card front">
    <div class="wordmark">Tobin<br>Vashley</div>
    <span class="deco-rule" aria-hidden="true"></span>
    <h1 class="holder-name">Tobin Vashley</h1>
    <ul class="contact-list">
      <li>
        <svg viewBox="0 0 10 10" aria-hidden="true"><path d="M2 0.5 L3.6 0.5 L4.3 2.8 L3.2 3.7 Q4.2 5.9 6.3 6.8 L7.2 5.7 L9.5 6.4 L9.5 8 Q9.5 9.5 8 9.5 Q1 8.8 0.5 2 Q0.5 0.5 2 0.5 Z"/></svg>
        646-555-0148
      </li>
      <li>
        <svg viewBox="0 0 10 10" aria-hidden="true"><path d="M0.5 2 H9.5 V8.5 H0.5 Z M1 2.5 L5 5.5 L9 2.5" stroke="var(--paper-front)" stroke-width="0.9"/></svg>
        tobin@morvalquist.com
      </li>
      <li>
        <svg viewBox="0 0 10 10" aria-hidden="true"><circle cx="5" cy="5" r="4.6"/><path d="M2.5 3.5 Q4 2.5 4.5 4 Q6 4.5 5.5 6.5 Q4 7 3 5.5 Z M6.5 2 Q8 2.5 8 4 Q7 3.8 6.5 2 Z" fill="var(--paper-front)"/></svg>
        morvalquist.com
      </li>
    </ul>
  </section>

  <section class="card card--back" aria-label="Card back">
    <div class="wordmark">Tobin<br>Vashley</div>
    <span class="deco-rule" aria-hidden="true"></span>
    <ul class="social-list">
      <li><span class="social-mark" aria-hidden="true"></span>morvalquist.com</li>
      <li><span class="social-mark" aria-hidden="true"></span>morvalquist</li>
      <li><span class="social-mark" aria-hidden="true"></span>morvalquist</li>
      <li><span class="social-mark" aria-hidden="true"></span>morvalquist</li>
    </ul>
    <p class="roles">Bandleader, Guitarist,<br>Vocalist, Songwriter</p>
  </section>
</body>
</html>
```